Private Investigation Business Card Design

I need a business card for a new private investigation company named Brisk Inquiries. I perform mainly surveillance jobs, vehicle repossessions, document serves etc. The final design should aim for a professional look. The logo has a magnifying glass with stick man arms and legs and is in a running action to show the "Brisk" aspect of the name. If the colour scheme could remain the same as the website www.briskinquiries-demo.com.au with silvers,blacks and a couple electric blue highlights.
Industry/Entity Type
Business
Contact Information for Business Card
Morgan Kellaway
Brisk Inquiries
0487316204
PO Box 58, Carnwell NSW 2291
info@briskinquiries-demo.com.au
www.briskinquiries-demo.com.au
Look and feel

```html
<!DOCTYPE html>
<html lang="en">
<head>
<meta charset="utf-8">
<title>Brisk Inquiries – Business Card</title>
<link rel="stylesheet" href="https://fonts.googleapis.com/css2?family=Open+Sans:wght@400;600;700&display=swap">
<style>
  :root {
    --backdrop: #3b332f;
    --card-black: #161616;
    --card-edge: #0c0c0c;
    --text-white: #f2f2f2;
    --text-grey: #b8b8b8;
    --silver: #c9cbcd;
    --divider: #3a3a3a;
    --mascot-light: #d9d9d9;
    --mascot-dark: #2a2a2a;
  }
  * { margin: 0; padding: 0; box-sizing: border-box; }
  html, body {
    width: 1200px; height: 844px; overflow: hidden;
    background: var(--backdrop);
    font-family: "Open Sans", sans-serif;
  }
  .canvas { position: relative; width: 1200px; height: 844px; }

  .card {
    position: absolute;
    width: 520px; height: 318px;
    top: 263px;
    background: var(--card-black);
    border: 1px solid var(--card-edge);
    box-shadow: 0 10px 24px rgba(0,0,0,0.45);
  }
  .card--back { left: 50px; }
  .card--front { left: 630px; background: #1c1a19; }

  /* back side */
  .mascot-area {
    position: absolute; left: 40px; top: 60px;
    width: 170px; height: 200px;
    border-radius: 6px;
    background: radial-gradient(circle at 55% 45%, var(--mascot-light) 0%, #6e6e6e 35%, var(--mascot-dark) 75%);
    opacity: 0.55;
  }
  .divider {
    position: absolute; left: 250px; top: 40px;
    width: 1px; height: 238px;
    background: var(--divider);
  }
  .contact {
    position: absolute; left: 272px; top: 58px;
    color: var(--text-white);
    font-size: 13px; line-height: 18px;
  }
  .contact__name { font-weight: 700; font-size: 15px; line-height: 19px; }
  .contact__company { color: var(--text-grey); margin-bottom: 14px; }
  .contact__address { margin-bottom: 12px; }
  .contact__line { display: flex; align-items: center; gap: 7px; }
  .contact__line svg { width: 10px; height: 10px; fill: var(--text-white); flex: none; }

  /* front side */
  .brand {
    position: absolute; left: 0; right: 0; top: 130px;
    display: flex; justify-content: center; align-items: center; gap: 14px;
  }
  .brand__name {
    font-weight: 700; font-size: 40px; letter-spacing: 1px;
    color: var(--silver);
  }
  .brand__dot {
    width: 22px; height: 22px; border-radius: 50%;
    background: var(--silver);
  }
</style>
</head>
<body>
<div class="canvas">

  <section class="card card--back">
    <div class="mascot-area" role="img" aria-label="Running magnifying-glass mascot with speed lines"></div>
    <div class="divider"></div>
    <div class="contact">
      <p class="contact__name">Morgan Kellaway</p>
      <p class="contact__company">Brisk Inquiries</p>
      <p class="contact__address">PO Box 58, Carnwell<br>NSW 2291</p>
      <p class="contact__line">
        <svg viewBox="0 0 10 10" aria-hidden="true"><path d="M2 1h2l1 2.5-1.2.8a5 5 0 0 0 1.9 1.9l.8-1.2L9 6v2a1 1 0 0 1-1 1A8 8 0 0 1 1 2a1 1 0 0 1 1-1z"/></svg>
        0487316204
      </p>
      <p class="contact__line">
        <svg viewBox="0 0 10 10" aria-hidden="true"><path d="M0 2h10v6H0z M0 2l5 3.5L10 2" stroke="#161616" stroke-width="0.8"/></svg>
        info@briskinquiries-demo.com.au
      </p>
      <p class="contact__line">
        <svg viewBox="0 0 10 10" aria-hidden="true"><path d="M4 6 6 4M3 5 1.5 6.5a1.8 1.8 0 0 0 2 2L5 7M7 5l1.5-1.5a1.8 1.8 0 0 0-2-2L5 3" stroke="#f2f2f2" stroke-width="1" fill="none"/></svg>
        www.briskinquiries-demo.com.au
      </p>
    </div>
  </section>

  <section class="card card--front">
    <div class="brand">
      <span class="brand__name">Brisk Inquiries</span>
      <span class="brand__dot"></span>
    </div>
  </section>

</div>
</body>
</html>
```